Business Cards for new orthopaedic surgery practice

My husband and I are starting our own orthopaedic surgery practice. We are looking for a business card that is uniform, but one will have my name/title and the other will have his. You can just create one design with my name on it for now. But when I choose your design as the winning design I will ask that you add another copy with his name/title.

We are looking for classy, simple, elite all in one. We like dark blues/a little gold/yellow. Something that goes with our logo. We want our logo incorporated. Here is all the info you need:
Business name: RV Bone & Vitality Center
Location: 38517 North Willowmere Ave
Maple Hollow, FL 33980
Phone: 954-218-4063
Fax: 954-582-7341
Email: info@myrvbonecare.example

Names: Lydia Vance, M.D.
Board Certified Hand and Upper Extremity Surgeon

Ebo Dansu, M.D.
Board Certified Hip & Knee Replacement/General Orthopaedic Surgeon

Can decide what you want to put on the back. Maybe a slogan:
Grounded in Skill. Built Around You

I am just going to upload our logo. The only thing is if we select you as the winning design, the location, and phone numbers may change. We will need your help to update that once fully solidified.

Industry/Entity Type

Medical

Contact Information for Business Card

Colors
0054AA
0677BA
7BADD7
CADEEF
E8F1F8
0094D4
00A9DD
6FCCEA
C7EBF8
E9F6FB

Requirements
Must have
• class, appeal,
Should not have
• We want to air on the side of masculine if we are looking at masculine vs. feminine feel. But we still want it classy, sophisticated, and something we will love

```html
<!DOCTYPE html>
<html lang="en">
<head>
<meta charset="utf-8">
<title>RV Bone &amp; Vitality Center — Business Card</title>
<link rel="stylesheet" href="https://fonts.googleapis.com/css2?family=Montserrat:wght@400;500;600;700&display=swap">
<style>
  :root {
    --backdrop: #e0e0e0;
    --navy: #13254d;
    --navy-ink: #1c2b55;
    --gold: #c9924a;
    --rule-gold: #b09a72;
    --tagline: #8f95d8;
    --paper: #ffffff;
    --ink: #111111;
    --muted: #555555;
  }
  * { margin: 0; padding: 0; box-sizing: border-box; }
  html, body {
    width: 1200px; height: 1200px; overflow: hidden;
    background: var(--backdrop);
    font-family: "Montserrat", sans-serif;
  }
  .card {
    position: absolute;
    left: 180px;
    width: 867px;
    height: 498px;
  }
  .card-front { top: 85px; background: var(--navy); }
  .card-back { top: 622px; background: var(--paper); }

  .front-mark {
    position: absolute;
    left: 0; right: 0; top: 170px;
    text-align: center;
    color: var(--gold);
    font-weight: 600;
    font-size: 38px;
    line-height: 1.25;
    letter-spacing: 0.5px;
  }
  .front-tagline {
    position: absolute;
    left: 0; right: 0; top: 418px;
    text-align: center;
    color: var(--tagline);
    font-size: 30px;
    font-weight: 500;
  }

  .practice-name {
    position: absolute;
    left: 46px; top: 34px;
    font-size: 36px; font-weight: 600;
    color: var(--ink);
    letter-spacing: 0.6px;
    white-space: nowrap;
  }
  .practice-rule {
    position: absolute;
    left: 46px; top: 96px;
    width: 559px; height: 6px;
    background: var(--rule-gold);
  }
  .doctor-name {
    position: absolute;
    left: 46px; top: 127px;
    font-size: 32px; font-weight: 600;
    color: var(--navy-ink);
  }
  .doctor-title {
    position: absolute;
    left: 46px; top: 175px;
    font-size: 22px; line-height: 31px;
    color: var(--muted);
  }
  .back-mark {
    position: absolute;
    right: 47px; top: 40px;
    width: 180px;
    text-align: right;
    color: var(--navy-ink);
    font-weight: 600;
    font-size: 26px;
    line-height: 1.2;
  }
  .contact-list {
    position: absolute;
    left: 46px; top: 325px;
    list-style: none;
    font-size: 22px; line-height: 37.5px;
    color: var(--muted);
    white-space: nowrap;
  }
  .contact-label {
    font-size: 25px; font-weight: 500;
    color: var(--navy-ink);
    margin-right: 6px;
  }
  .address {
    position: absolute;
    right: 47px; top: 405px;
    text-align: right;
    font-style: normal;
    font-size: 22px; line-height: 31px;
    color: var(--muted);
    white-space: nowrap;
  }
</style>
</head>
<body>
  <section class="card card-front" aria-label="Card front">
    <div class="front-mark">RV Bone &amp;<br>Vitality Center</div>
    <p class="front-tagline">Grounded in Skill. Built Around You</p>
  </section>

  <section class="card card-back" aria-label="Card back">
    <h1 class="practice-name">RV Bone &amp; Vitality Center</h1>
    <div class="practice-rule"></div>
    <h2 class="doctor-name">Lydia Vance, M.D.</h2>
    <p class="doctor-title">Board Certified Hand and<br>Upper Extremity Surgeon</p>
    <div class="back-mark">RV Bone &amp;<br>Vitality<br>Center</div>
    <ul class="contact-list">
      <li><span class="contact-label">Phone.</span> 954-218-4063</li>
      <li><span class="contact-label">Fax.</span> 954-582-7341</li>
      <li><span class="contact-label">Email.</span> info@myrvbonecare.example</li>
      <li><span class="contact-label">Website.</span> myrvbonecare.example</li>
    </ul>
    <address class="address">38517 North Willowmere Ave<br>Maple Hollow, FL 33980</address>
  </section>
</body>
</html>
```